Larkspur Talent IT Recruiting firm needs a business card design for Recruiters, Sourcers, and Account

We need business cards that allow us to change all contact info, names, titles (Recruiter, Sourcer, Account Manager, Director, CEO, etc) per person since we have three offices, in three cities, Phoenix, Austin, and Las Vegas. We do recruiting and contractors for IT positions (Developers, Architects, Software Engineers, Security Engineers, Help Desk, DBAs, PMs, Scrum Masters, etc.) Our client companies are very diverse from Meridian 100 to silicone Valley type start-ups.

So, while we what hip, techie, and quirky, it still needs to be professional. Primary color we use is blue, with silver as a secondary color.

Target Market(s)

IT, Technology

Industry/Entity Type

Business

Contact Information for Business Card

Company name: Larkspur Talent, Inc.
Website: www.larkspurtalent.example
Logos for Careerloop, Blipster, and Myriada

Name, Title, Office Number, Cell Number, email

Font styles to use
Serif
Sans Serif

Colors
0455a3
d5d5d5

Requirements
Nice to have
• The grey I selected below is not necessary - but, would like silver included. I included a card design (File 3: LTI early trial example.jpg) that I had started on. It's very rough, and not quite what we're looking for, but what we did like is the logo, big, maybe a bit faded, off center, goes out of frame, etc. Still looking for other ideas - you are the pros! But, just an idea of a design element we liked.

```html
<!DOCTYPE html>
<html lang="en">
<head>
<meta charset="utf-8">
<title>Larkspur Talent – Business Card</title>
<link rel="stylesheet" href="https://fonts.googleapis.com/css2?family=Arvo:wght@700&family=Cinzel:wght@400&family=Lato:wght@300;400&display=swap">
<style>
  :root {
    --brand-blue: #0455a3;
    --bright-blue: #1f7fd6;
    --ink: #1c1c1c;
    --text-dark: #2a2a2a;
    --silver: #d5d5d5;
    --backdrop: #e9e9e9;
    --card: #ffffff;
  }
  * { margin: 0; padding: 0; box-sizing: border-box; }
  html, body { width: 1200px; height: 900px; overflow: hidden; }
  body { background: var(--backdrop); position: relative; font-family: "Lato", sans-serif; }

  .card {
    position: absolute;
    left: 250px;
    width: 700px;
    height: 400px;
    background: var(--card);
    box-shadow: 0 6px 18px rgba(0,0,0,0.18);
    overflow: hidden;
  }
  .card--front { top: 40px; }
  .card--back { top: 460px; }

  .rule { position: absolute; height: 2px; background: var(--brand-blue); }

  .wordmark {
    position: absolute;
    display: flex;
    align-items: center;
    gap: 14px;
  }
  .wordmark__dot {
    width: 46px; height: 46px; border-radius: 50%;
    background: var(--bright-blue);
  }
  .wordmark__name {
    font-family: "Lato", sans-serif;
    font-weight: 300;
    color: var(--ink);
    letter-spacing: 6px;
    text-transform: uppercase;
    line-height: 1;
  }
  .tagline {
    position: absolute;
    font-family: "Cinzel", serif;
    color: var(--text-dark);
    letter-spacing: 4px;
    text-transform: uppercase;
    white-space: nowrap;
  }

  /* front */
  .card--front .wordmark { left: 0; right: 0; top: 118px; justify-content: center; }
  .card--front .wordmark__name { font-size: 44px; }
  .card--front .tagline { left: 0; right: 0; top: 210px; text-align: center; font-size: 19px; }
  .website {
    position: absolute;
    right: 40px;
    top: 280px;
    font-family: "Cinzel", serif;
    font-size: 11px;
    letter-spacing: 1.5px;
    color: var(--text-dark);
  }

  /* back */
  .person { position: absolute; left: 70px; top: 62px; }
  .person__name {
    font-family: "Arvo", serif; font-weight: 700;
    font-size: 18px; color: var(--ink); letter-spacing: 1px;
    text-transform: uppercase;
  }
  .person__title {
    font-family: "Lato", sans-serif; font-size: 10px;
    color: var(--brand-blue); text-align: right; letter-spacing: 1px;
  }
  .card--back .wordmark { right: 40px; top: 112px; }
  .card--back .wordmark__dot { width: 34px; height: 34px; }
  .card--back .wordmark__name { font-size: 30px; letter-spacing: 4px; }
  .card--back .tagline { right: 40px; top: 168px; font-size: 13px; letter-spacing: 3px; }

  .contact-list { position: absolute; left: 48px; top: 226px; list-style: none; }
  .contact-list li {
    display: flex; align-items: center; gap: 14px;
    height: 21px;
    font-family: "Arvo", serif; font-weight: 700;
    font-size: 11px; letter-spacing: 0.6px;
    color: var(--ink); text-transform: uppercase;
  }
  .contact-list .icon { width: 11px; height: 11px; flex: none; }
  .contact-list .icon--dot { border-radius: 50%; background: var(--brand-blue); }
</style>
</head>
<body>

  <section class="card card--front" aria-label="Card front">
    <div class="wordmark">
      <span class="wordmark__dot"></span>
      <span class="wordmark__name">Larkspur Talent</span>
    </div>
    <p class="tagline">Growing the Right Teams</p>
    <span class="rule" style="left:0; top:330px; width:420px;"></span>
    <span class="rule" style="left:440px; top:300px; right:0;"></span>
    <p class="website">WWW.LARKSPURTALENT.EXAMPLE</p>
    <span class="rule" style="left:0; right:0; top:392px; height:3px;"></span>
  </section>

  <section class="card card--back" aria-label="Card back">
    <span class="rule" style="left:0; top:86px; width:62px;"></span>
    <div class="person">
      <p class="person__name">Dana R. Whitlock</p>
      <p class="person__title">CEO</p>
    </div>
    <span class="rule" style="left:320px; top:58px; right:0;"></span>

    <div class="wordmark">
      <span class="wordmark__dot"></span>
      <span class="wordmark__name">Larkspur Talent</span>
    </div>
    <p class="tagline">Growing the Right Teams</p>

    <ul class="contact-list">
      <li><span class="icon icon--dot"></span>myriada.example/Dana R. Whitlock</li>
      <li><span class="icon icon--dot"></span>blipster.example/Dana R. Whitlock</li>
      <li><span class="icon icon--dot"></span>careerloop.example/Dana R. Whitlock</li>
      <li>
        <svg class="icon" viewBox="0 0 24 24" aria-hidden="true"><path fill="#0455a3" d="M6.6 10.8a15 15 0 0 0 6.6 6.6l2.2-2.2a1 1 0 0 1 1-.25 11.4 11.4 0 0 0 3.6.57 1 1 0 0 1 1 1V20a1 1 0 0 1-1 1A17 17 0 0 1 3 4a1 1 0 0 1 1-1h3.5a1 1 0 0 1 1 1c0 1.25.2 2.45.57 3.570a1 1 0 0 1-.25 1z"/></svg>
        555-014-2290
      </li>
      <li>
        <svg class="icon" viewBox="0 0 24 24" aria-hidden="true"><rect x="6" y="2" width="12" height="20" rx="2" fill="none" stroke="#0455a3" stroke-width="2.4"/><circle cx="12" cy="18" r="1.4" fill="#0455a3"/></svg>
        555-014-2291
      </li>
      <li>
        <svg class="icon" viewBox="0 0 24 24" aria-hidden="true"><rect x="2" y="5" width="20" height="14" rx="1" fill="#0455a3"/><path d="M2 6l10 7 10-7" fill="none" stroke="#fff" stroke-width="1.8"/></svg>
        danawhitlock@larkspurtalent.example
      </li>
      <li><span class="icon icon--dot"></span>www.larkspurtalent.example</li>
    </ul>
  </section>

</body>
</html>
```